New Design for Willow Glow & Laser

The name of our company is Willow Glow & Laser, and this is our current website: www.WillowGlowLaser.example. We are looking for a fresh design mock-up of our website.
What is important to us?
> We want to maintain the same navigation.
> We want to use the same content (e.g., text, pictures, etc.)
> We want to maintain the color scheme.
> The website aims to get visitors to BOOK ONLINE or BUY ONLINE.
Essential instructions for designers:
> Please visit our current website and our social media accounts to get a better idea of our brand design.
> We want a mockup design for our home page, service page, pricing page, before & after page, shop deals page, careers page, contact pages, and blog pages.
> Color codes: #faa641, #222222, #fffffe, #ea8103
Target Market(s)
women 25 - 45
Number of Pages Required
5+ page

```html
<!DOCTYPE html>
<html lang="en">
<head>
<meta charset="utf-8">
<title>Willow Glow &amp; Laser — Home</title>
<link href="https://fonts.googleapis.com/css2?family=Montserrat:wght@600;700;800&family=Roboto:ital,wght@0,400;0,500;0,700;1,400&family=Michroma&display=swap" rel="stylesheet">
<style>
:root{
  --orange:#faa641;
  --orange-deep:#ea8103;
  --ink:#222222;
  --paper:#fffffe;
  --grey-text:#5f5f5f;
  --line:#d9d9d9;
}
*{margin:0;padding:0;box-sizing:border-box}
html,body{width:1200px;height:3554px;overflow:hidden;background:var(--paper)}
body{position:relative;font-family:'Roboto',sans-serif;color:var(--ink)}
a{color:inherit;text-decoration:none}

/* header */
.site-header{position:absolute;left:0;top:0;width:1200px;height:83px;background:var(--paper)}
.nav-item{position:absolute;top:31px;font-size:13.5px;font-weight:500;letter-spacing:.3px;text-transform:uppercase}
.nav-sep{position:absolute;top:30px;font-size:13.5px}
.brand{position:absolute;display:flex;align-items:center;gap:8px;font-family:'Montserrat',sans-serif;font-weight:800;color:var(--ink)}
.brand-dot{width:22px;height:22px;border-radius:50%;background:var(--orange)}
.btn{position:absolute;display:flex;align-items:center;justify-content:center;gap:8px;border-radius:24px;font-size:13.5px;font-weight:500;text-transform:uppercase;color:var(--paper)}
.btn-orange{background:var(--orange)}
.btn-dark{background:var(--ink);border:2px solid var(--orange)}
.btn svg{width:13px;height:13px}

/* hero */
.hero{position:absolute;left:0;top:83px;width:1200px;height:605px;
  background:
    radial-gradient(ellipse 180px 160px at 830px 130px,#6a4a3a 0%,rgba(106,74,58,0) 100%),
    radial-gradient(ellipse 150px 170px at 960px 380px,#c99a80 0%,rgba(201,154,128,0) 100%),
    radial-gradient(ellipse 330px 330px at 760px 430px,#2b2a2a 0%,rgba(43,42,42,0) 100%),
    radial-gradient(ellipse 260px 250px at 1060px 560px,#3a3b3e 0%,rgba(58,59,62,0) 100%),
    linear-gradient(100deg,#ebeae8 0%,#e1dfdd 45%,#cfcac6 62%,#bdb6b0 100%)}
.hero-title{position:absolute;left:142px;top:262px;font-family:'Montserrat',sans-serif;font-weight:800;font-size:58px;line-height:56px;color:#2b2b2b}
.hero-sub{position:absolute;left:142px;top:389px;font-size:14px;line-height:24px;color:#333;width:380px}

/* about */
.about-mark{position:absolute;left:184px;top:815px;width:290px;height:290px;border-radius:50%;background:var(--orange)}
.about-title{position:absolute;left:589px;top:786px;width:460px;font-family:'Montserrat',sans-serif;font-weight:700;font-size:32px;line-height:36px;text-transform:uppercase}
.about-copy{position:absolute;left:589px;top:866px;width:440px;font-size:14.5px;line-height:23px;color:var(--grey-text)}
.about-copy p{margin-bottom:7px}

.section-title{position:absolute;left:0;width:1200px;text-align:center;font-family:'Montserrat',sans-serif;font-weight:700;font-size:32px;text-transform:uppercase}

/* offers */
.offer{position:absolute;top:1289px;width:288px;height:331px}
.offer-label{position:absolute;left:0;bottom:30px;width:100%;text-align:center;color:var(--paper);font-weight:700;font-size:17px;text-shadow:0 1px 4px rgba(0,0,0,.5)}
.offer-photofacial{background:radial-gradient(ellipse 140px 120px at 160px 140px,#d9b49a 0%,rgba(217,180,154,0) 100%),linear-gradient(135deg,#6f625a 0%,#c6a48c 45%,#9a8e88 70%,#3d3735 100%)}
.offer-facial{background:radial-gradient(ellipse 90px 90px at 170px 90px,#e0bfa8 0%,rgba(224,191,168,0) 100%),radial-gradient(ellipse 130px 110px at 200px 180px,#1f1d1d 0%,rgba(31,29,29,0) 100%),linear-gradient(160deg,#e8e6e4 0%,#d7d3cf 50%,#8c8580 80%,#3a3636 100%)}
.offer-lip{background:radial-gradient(ellipse 110px 130px at 200px 230px,#dcb7a0 0%,rgba(220,183,160,0) 100%),radial-gradient(ellipse 130px 120px at 90px 120px,#1e1c1c 0%,rgba(30,28,28,0) 100%),linear-gradient(150deg,#3b3735 0%,#85807c 45%,#b8afa9 70%,#2a2625 100%)}
.offer-feature{background:var(--orange);color:var(--paper);text-align:center;padding:36px 22px 0}
.offer-feature h3{font-size:18px;font-weight:700;margin-bottom:10px}
.offer-feature p{font-size:12px;line-height:27.3px}
.offer-feature .more{display:inline-block;margin-top:8px;font-size:12.5px;font-weight:700;text-decoration:underline}

/* gallery */
.gallery-tile{position:absolute;width:276px;height:167px}
.g1{background:radial-gradient(ellipse 60px 70px at 170px 70px,#c99a7e 0%,rgba(201,154,126,0) 100%),radial-gradient(ellipse 80px 60px at 50px 60px,#1f1f1f 0%,rgba(31,31,31,0) 100%),linear-gradient(135deg,#dad8d5,#bdb8b3 60%,#2c2a29)}
.g2{background:radial-gradient(ellipse 50px 60px at 100px 80px,#d9b28f 0%,rgba(217,178,143,0) 100%),radial-gradient(ellipse 70px 70px at 110px 130px,#1d1b1b 0%,rgba(29,27,27,0) 100%),linear-gradient(135deg,#e6e3df,#cfc9c4 60%,#b8aea6)}
.g3{background:radial-gradient(ellipse 60px 80px at 110px 110px,#3d5866 0%,rgba(61,88,102,0) 100%),radial-gradient(ellipse 60px 80px at 190px 110px,#c9b29c 0%,rgba(201,178,156,0) 100%),linear-gradient(135deg,#ece9e5,#d6d1cc 55%,#5c6b4a)}
.g4{background:radial-gradient(ellipse 90px 70px at 120px 90px,#1c1b1b 0%,rgba(28,27,27,0) 100%),linear-gradient(135deg,#dedbd7,#bfb9b4 60%,#6f6965)}
.g5{background:radial-gradient(ellipse 70px 80px at 80px 110px,#1d1c1c 0%,rgba(29,28,28,0) 100%),radial-gradient(ellipse 60px 60px at 200px 120px,#cbb1a0 0%,rgba(203,177,160,0) 100%),linear-gradient(135deg,#e5e1dc,#c7bfb6 60%,#8d847c)}
.g6{background:radial-gradient(ellipse 120px 90px at 150px 90px,#d8b7a3 0%,rgba(216,183,163,0) 100%),radial-gradient(ellipse 80px 110px at 250px 60px,#1a1818 0%,rgba(26,24,24,0) 100%),linear-gradient(135deg,#dfe4e8,#b8c2c8 60%,#6f7378)}

/* testimonials */
.reviews{position:absolute;left:0;top:2205px;width:1200px;height:375px;background:radial-gradient(ellipse 300px 260px at 160px 200px,#f29f3a 0%,rgba(242,159,58,0) 100%),radial-gradient(ellipse 260px 260px at 880px 220px,#f3a13e 0%,rgba(243,161,62,0) 100%),var(--orange)}
.reviews-title{position:absolute;left:0;top:82px;width:1200px;text-align:center;font-family:'Michroma',sans-serif;font-size:30px;letter-spacing:3px;color:var(--paper);text-transform:uppercase}
.review{position:absolute;top:150px;width:430px;color:var(--paper)}
.review svg{width:24px;height:20px;margin-bottom:14px}
.review p{font-style:italic;font-size:14.5px;line-height:25px;padding-bottom:14px;border-bottom:1px solid rgba(255,255,254,.7)}
.review .who{margin-top:20px;font-size:15px;font-weight:500}

/* contact */
.contact-block{position:absolute;left:134px;top:2668px;width:418px;height:359px;background:var(--orange);padding:103px 30px 0}
.contact-kicker{font-size:17px;font-weight:500;color:var(--paper);margin-bottom:20px}
.contact-lead{font-weight:700;font-size:29px;line-height:45px;color:var(--paper);text-transform:uppercase}
.contact-frame{position:absolute;left:724px;top:2686px;width:342px;height:323px;border:4px solid var(--orange)}
.contact-card{position:absolute;left:463px;top:2717px;width:582px;height:404px;background:var(--paper);box-shadow:0 6px 30px rgba(0,0,0,.12)}
.card-title{position:absolute;left:49px;top:40px;font-family:'Michroma',sans-serif;font-size:22px;font-weight:400;letter-spacing:2px;text-transform:uppercase}
.field{position:absolute;width:214px}
.field label{display:block;font-size:14px;font-weight:500;margin-bottom:12px}
.field span{display:block;font-size:11px;color:#888;padding:0 0 10px 2px;border-bottom:1px solid var(--line)}
.send{position:absolute;left:468px;top:301px;width:60px;height:60px;border-radius:50%;background:var(--orange);display:flex;align-items:center;justify-content:center}

/* footer */
.site-footer{position:absolute;left:0;top:3201px;width:1200px;height:353px;background:var(--ink);color:var(--paper)}
.foot-head{position:absolute;top:65px;font-size:14px;font-weight:700;text-transform:uppercase}
.foot-head::after{content:"";display:block;width:58px;height:2px;background:var(--paper);margin-top:10px}
.foot-links{position:absolute;left:400px;top:106px;list-style:none;font-size:11.5px;line-height:28.7px}
.foot-contact{position:absolute;left:567px;display:flex;align-items:center;gap:12px;font-size:11.5px;line-height:19px}
.icon-disc{width:24px;height:24px;border-radius:50%;background:#444;display:flex;align-items:center;justify-content:center;flex:none}
.subscribe{position:absolute;left:820px;top:106px;width:220px;font-size:11.5px;line-height:19px}
.sub-input{position:absolute;left:820px;top:158px;width:235px;height:32px;border-radius:16px;background:var(--paper);overflow:hidden}
.sub-input span{position:absolute;left:14px;top:9px;font-size:10px;color:#888}
.sub-input i{position:absolute;right:0;top:0;width:44px;height:32px;background:var(--orange);display:flex;align-items:center;justify-content:center}
.social{position:absolute;top:212px;width:28px;height:28px;border-radius:50%;background:var(--paper)}
.chat{position:absolute;left:1093px;top:234px;width:38px;height:38px;border-radius:50%;background:var(--orange)}
.copy{position:absolute;top:317px;font-size:12.5px}
</style>
</head>
<body>

<header class="site-header">
  <a class="nav-item" style="left:142px">Home</a><span class="nav-sep" style="left:205px">|</span>
  <a class="nav-item" style="left:232px">Services</a><span class="nav-sep" style="left:318px">|</span>
  <a class="nav-item" style="left:344px">Pricing</a><span class="nav-sep" style="left:421px">|</span>
  <a class="nav-item" style="left:448px">About</a>
  <div class="brand" style="left:514px;top:24px;font-size:25px"><span class="brand-dot"></span>WILLOW</div>
  <a class="nav-item" style="left:741px">Blog</a><span class="nav-sep" style="left:800px">|</span>
  <a class="nav-item" style="left:826px">Contact</a>
  <a class="btn btn-orange" style="left:921px;top:21px;width:134px;height:37px;font-size:14px">Book Online</a>
</header>

<section class="hero" role="img" aria-label="Photo: a smiling aesthetician leans beside a happy client who holds a hand mirror after a skin treatment"></section>
<h1 class="hero-title">YOUR SKIN<br>DESERVES IT</h1>
<p class="hero-sub">Laser Center &amp; Medispa Located In Downtown Phoenix, Tempe, Tucson, &amp; Yuma.</p>
<a class="btn btn-dark" style="left:142px;top:458px;width:157px;height:44px">Book Online <svg viewBox="0 0 16 16"><circle cx="8" cy="8" r="8" fill="#fffffe"/><path d="M6 4.5 9.5 8 6 11.5" stroke="#222" stroke-width="2" fill="none"/></svg></a>
<a class="btn btn-orange" style="left:305px;top:458px;width:156px;height:44px">Shop Deals <svg viewBox="0 0 16 16"><circle cx="8" cy="8" r="8" fill="#fffffe"/><path d="M6 4.5 9.5 8 6 11.5" stroke="#faa641" stroke-width="2" fill="none"/></svg></a>

<div class="about-mark" role="img" aria-label="Willow Glow &amp; Laser brand circle"></div>
<h2 class="about-title">About Willow Glow &amp; Laser</h2>
<div class="about-copy">
  <p>At Willow Glow &amp; Laser, we’ve always believed that caring about your skin and your appearance is not selfish, it is self-care. It’s time to be proud of the steps you take to look your best and it’s time you ask for the best. Your skin deserves it.</p>
  <p>Willow brings to you the latest technology, techniques, and the best professionals to deliver the results you want guaranteed.</p>
  <p>It’s time to cross out the judgment, the labels, the hesitation, and the regrets.</p>
</div>
<a class="btn btn-orange" style="left:589px;top:1076px;width:149px;height:39px">Learn More <svg viewBox="0 0 16 16"><circle cx="8" cy="8" r="8" fill="#fffffe"/><path d="M6 4.5 9.5 8 6 11.5" stroke="#faa641" stroke-width="2" fill="none"/></svg></a>

<h2 class="section-title" style="top:1212px">What We Offer</h2>
<div class="offer offer-photofacial" style="left:0" role="img" aria-label="Photo: client in protective goggles receiving a photofacial"><span class="offer-label">Photofacials</span></div>
<div class="offer offer-facial" style="left:304px" role="img" aria-label="Photo: aesthetician performing a facial treatment"><span class="offer-label">Facials &amp; Peels</span></div>
<div class="offer offer-feature" style="left:607px">
  <h3>Laser Hair Removal</h3>
  <p>Ouch! You know that you’re tired of the same old same old with your hair removal routine. Let’s be real. You go to shave your legs (or chest or, wink, wink, other body parts) right before that big date and end up bleeding like crazy with a bunch of tissues sticking to your legs.</p>
  <a class="more">Read More</a>
</div>
<div class="offer offer-lip" style="left:912px" role="img" aria-label="Photo: gloved hands performing a lip enhancement"><span class="offer-label" style="bottom:34px">Lip Shape &amp; Enhancement</span></div>

<h2 class="section-title" style="top:1700px">Our Gallery</h2>
<div class="gallery-tile g1" style="left:161px;top:1771px" role="img" aria-label="Gallery photo: client with a hand mirror"></div>
<div class="gallery-tile g2" style="left:462px;top:1771px" role="img" aria-label="Gallery photo: aesthetician treating a client"></div>
<div class="gallery-tile g3" style="left:762px;top:1771px" role="img" aria-label="Gallery photo: two staff members holding product"></div>
<div class="gallery-tile g4" style="left:161px;top:1958px" role="img" aria-label="Gallery photo: injection treatment in progress"></div>
<div class="gallery-tile g5" style="left:462px;top:1958px" role="img" aria-label="Gallery photo: consultation with a tablet"></div>
<div class="gallery-tile g6" style="left:762px;top:1958px" role="img" aria-label="Gallery photo: close view of treated skin"></div>

<section class="reviews">
  <h2 class="reviews-title">What Our Happy Clients Say</h2>
  <div class="review" style="left:145px">
    <svg viewBox="0 0 24 20"><path d="M0 20V10C0 4 3 1 9 0v4C6 5 5 7 5 10h5v10zM14 20V10c0-6 3-9 9-10v4c-3 1-4 3-4 6h5v10z" fill="#fffffe"/></svg>
    <p>She explained the procedure to me, answered all questions and did a great job at making me feel at ease. I would absolutely recommend Willow Glow &amp; Laser.</p>
    <div class="who">Carla R.</div>
  </div>
  <div class="review" style="left:629px">
    <svg viewBox="0 0 24 20"><path d="M0 20V10C0 4 3 1 9 0v4C6 5 5 7 5 10h5v10zM14 20V10c0-6 3-9 9-10v4c-3 1-4 3-4 6h5v10z" fill="#fffffe"/></svg>
    <p>“Awesome experience! Clean, professional, fast and painless laser hair removal services. Tessa was a great technician and the whole experience was stress-free!”</p>
    <div class="who">Nadia P.</div>
  </div>
</section>

<div class="contact-block">
  <div class="contact-kicker">CONTACT US</div>
  <div class="contact-lead">If you have any<br>questions ,please<br>contact us</div>
</div>
<div class="contact-frame"></div>
<form class="contact-card">
  <h2 class="card-title">Get in Touch</h2>
  <div class="field" style="left:53px;top:100px"><label>Your Name</label><span>John Smith</span></div>
  <div class="field" style="left:311px;top:100px"><label>Location</label><span>Lorem ipsum dolor sit amet</span></div>
  <div class="field" style="left:53px;top:187px"><label>Email Address</label><span>John Smith@gmail.com</span></div>
  <div class="field" style="left:311px;top:187px"><label>Phone</label><span>01122-123-456-789</span></div>
  <div class="field" style="left:53px;top:274px;width:425px"><label>Message</label><span style="padding-bottom:32px">Hi, do you have a moment to talk abo...|</span></div>
  <div class="send"><svg width="22" height="22" viewBox="0 0 24 24"><path d="M22 2 2 10l7 3 3 8z" fill="#fffffe"/></svg></div>
</form>

<footer class="site-footer">
  <div class="brand" style="left:142px;top:62px;font-size:34px;color:var(--paper)"><span class="brand-dot" style="width:28px;height:28px"></span>WILLOW</div>
  <div class="foot-head" style="left:400px">Quick Links</div>
  <ul class="foot-links"><li>Home</li><li>Services</li><li>Pricing</li><li>About</li><li>Blog</li><li>Contact</li></ul>
  <div class="foot-head" style="left:567px">Contact Us</div>
  <div class="foot-contact" style="top:110px"><span class="icon-disc"><svg width="12" height="12" viewBox="0 0 24 24"><path d="M6 2h4l2 5-3 2a12 12 0 0 0 6 6l2-3 5 2v4a2 2 0 0 1-2 2A19 19 0 0 1 4 4a2 2 0 0 1 2-2z" fill="#fffffe"/></svg></span>(555) 013-2288</div>
  <div class="foot-contact" style="top:153px"><span class="icon-disc"><svg width="12" height="12" viewBox="0 0 24 24"><rect x="2" y="5" width="20" height="14" rx="2" fill="#fffffe"/><path d="M2 6l10 7 10-7" stroke="#444" stroke-width="2" fill="none"/></svg></span>hello@willowglowlaser.example</div>
  <div class="foot-contact" style="top:194px"><span class="icon-disc"><svg width="12" height="12" viewBox="0 0 24 24"><path d="M12 2a7 7 0 0 0-7 7c0 5 7 13 7 13s7-8 7-13a7 7 0 0 0-7-7z" fill="#fffffe"/><circle cx="12" cy="9" r="2.5" fill="#444"/></svg></span>118 Orchard Lane<br>Suite 40 Tucson, AZ 85700</div>
  <div class="foot-head" style="left:815px">Subscribe To Our Blog</div>
  <p class="subscribe">Sign up today to get resources on how to attract and retain more customers!</p>
  <div class="sub-input"><span>✉ Email Address</span><i><svg width="14" height="14" viewBox="0 0 24 24"><path d="M22 2 2 10l7 3 3 8z" fill="#fffffe"/></svg></i></div>
  <span class="social" style="left:817px" aria-label="Social profile"></span>
  <span class="social" style="left:850px" aria-label="Social profile"></span>
  <span class="chat" aria-label="Chat"></span>
  <div class="copy" style="left:142px">Copyright© 2024 Willow Glow Laser &nbsp;| &nbsp;All Rights Reserved</div>
  <div class="copy" style="left:795px">Specifications &nbsp;| &nbsp;&nbsp;Site Map &nbsp;| &nbsp;&nbsp;Privacy Policy</div>
</footer>

</body>
</html>
```